hello! I need a very simple modern business card for a new venture called The Quiet Harbour Retreats. It's the very first Tech-Free retreat in Asia!

The concept is very unique. Basically a group of 12-15 people would go on a 3 to 4 days retreat where no phone or internet is allowed. The first retreat will take place in a beautiful villa in Bali by the sea. It will include yoga, meditation, art & writing workshops, swimming, hiking, cooking, healthy vegetarian meals, etc.

Reason: Thanks for your submissions. I still haven't found exactly what I'm after but the designs that haven't be eliminated are getting close.. Please keep in mind that it should be a simple, modern and upmarket business card. Thanks

Target Market(s)

Both men and women who would like to disconnect from life, computer and phone for 3/4 days. They can be either local or expats but based in Asia (Singapore, Hong Kong).
Client will have to pay for their own flight and then the price is around US$600 for a 3-day retreat including everything (accommodation, food, activities). It means clients already have a good income. They are usually working in marketing, advertising, digital media, public relations.

Industry/Entity Type

Internet

Font styles to use
Other font styles liked:
• anything modern you like

Colors
acd036
9bcb3c
f37022
f68d4d
1b1b1b
333333
acd037

Requirements
Must have
• Name: Rell Vonta
Position: #screenwanderer
Company: The Quiet Harbour Retreats (asia should be smaller than the rest)
- Email button - quietharbourretreats@mailora.com
- Facebook button - www.pagenook.com/quietharbourretreats
- Eventbrite button - www.quietharbourretreats.ticketvale.com
Nice to have
• You can use my logo attached but it's something I designed quickly on Power Point so it would be nice to include your own version.
Should not have
• anything tacky or girly or childish. thanks

```html
<!DOCTYPE html>
<html lang="en">
<head>
<meta charset="utf-8">
<title>The Quiet Harbour Retreats – Business Card</title>
<link rel="stylesheet" href="https://fonts.googleapis.com/css2?family=Nunito+Sans:wght@300;400&display=swap">
<style>
  :root {
    --canvas: #ffffff;
    --card: #ffffff;
    --ink: #1b1b1b;
    --ink-soft: #333333;
    --leaf-green: #acd036;
    --sunset: #f68d4d;
    --sunset-deep: #f37022;
    --social-blue: #3d62a3;
  }
  * { margin: 0; padding: 0; box-sizing: border-box; }
  html, body {
    width: 1200px; height: 1000px; overflow: hidden;
    background: var(--canvas);
    font-family: "Nunito Sans", Arial, sans-serif;
    color: var(--ink);
  }
  .stage { position: relative; width: 1200px; height: 1000px; }
  .card {
    position: absolute; left: 291px; width: 605px; height: 349px;
    background: var(--card);
    box-shadow: 0 2px 6px rgba(0,0,0,0.22);
  }
  .card--front { top: 111px; }
  .card--back { top: 516px; }

  .brand-mark {
    position: absolute; border-radius: 50%;
    background: var(--leaf-green);
  }
  .card--front .brand-mark { left: 78px; top: 78px; width: 62px; height: 62px; }
  .card--back .brand-mark { left: 258px; top: 138px; width: 62px; height: 62px; }

  .holder {
    position: absolute; right: 38px; top: 34px; text-align: right;
  }
  .holder-name { font-size: 18px; font-weight: 400; color: var(--ink); line-height: 1.3; }
  .holder-role { font-size: 15px; font-weight: 300; color: var(--ink-soft); line-height: 1.3; }

  .company-name {
    position: absolute; left: 154px; top: 148px;
    font-size: 29px; font-weight: 300; letter-spacing: 0.3px;
    white-space: nowrap; color: var(--ink);
  }

  .contact-list { position: absolute; left: 166px; top: 206px; list-style: none; }
  .contact-item {
    display: flex; align-items: center; height: 33px;
    font-size: 18.5px; font-weight: 300; color: var(--ink-soft);
    white-space: nowrap;
  }
  .contact-icon { width: 31px; height: 28px; margin-right: 10px; flex: none; display: flex; align-items: center; justify-content: center; }
  .contact-icon .square { width: 28px; height: 28px; border-radius: 4px; display: block; }
  .square--social { background: var(--social-blue); }
  .square--tickets { background: var(--sunset-deep); }

  .back-signature {
    position: absolute; right: 38px; top: 298px;
    font-size: 19px; font-weight: 300; color: var(--ink-soft); white-space: nowrap;
  }
</style>
</head>
<body>
<main class="stage">
  <section class="card card--front" aria-label="Card front">
    <div class="holder">
      <p class="holder-name">Rell Vonta</p>
      <p class="holder-role">#screenwanderer</p>
    </div>
    <span class="brand-mark" aria-hidden="true"></span>
    <h1 class="company-name">The Quiet Harbour Retreats</h1>
    <ul class="contact-list">
      <li class="contact-item">
        <span class="contact-icon">
          <svg width="31" height="21" viewBox="0 0 31 21" aria-hidden="true">
            <rect x="0" y="0" width="31" height="21" fill="var(--leaf-green)"/>
            <polyline points="1,1 15.5,12 30,1" fill="none" stroke="#fff" stroke-width="1.4"/>
            <line x1="1" y1="20" x2="11.5" y2="9.5" stroke="#fff" stroke-width="1.2"/>
            <line x1="30" y1="20" x2="19.5" y2="9.5" stroke="#fff" stroke-width="1.2"/>
          </svg>
        </span>
        quietharbourretreats@mailora.com
      </li>
      <li class="contact-item">
        <span class="contact-icon"><span class="square square--social"></span></span>
        www.pagenook.com/quietharbourretreats
      </li>
      <li class="contact-item">
        <span class="contact-icon"><span class="square square--tickets"></span></span>
        www.quietharbourretreats.ticketvale.com
      </li>
    </ul>
  </section>

  <section class="card card--back" aria-label="Card back">
    <span class="brand-mark" aria-hidden="true"></span>
    <p class="back-signature">The Quiet Harbour Retreats</p>
  </section>
</main>
</body>
</html>
```